Harborlight Amusement Collective (HAC)

We need a business card design for Harborlight Amusement Collective. Modern and sleek looking, with all critical information. Open to single or double sided designs, if double sided info needs to be all on one side. The main Logo is Harborlight Amusement collective and must be on the card. The other three logos are for the brands that fall under the group, they might be good on the back.

Industry/Entity Type

Business

```html
<!DOCTYPE html>
<html lang="en">
<head>
<meta charset="utf-8">
<title>Harborlight Amusement Collective – Business Card</title>
<link rel="stylesheet" href="https://fonts.googleapis.com/css2?family=Montserrat:wght@500;600&family=Fira+Sans+Condensed:wght@500&family=Nunito+Sans:wght@400&display=swap">
<style>
  :root {
    --page-bg: #d8d3cb;
    --card-bg: #f2f0eb;
    --brand-blue: #25508f;
    --band-blue: #2a5a98;
    --band-text: #e9eef5;
    --band-muted: #c9d6e8;
    --ink: #2a2a2a;
  }
  * { margin: 0; padding: 0; box-sizing: border-box; }
  html, body {
    width: 1200px; height: 1054px; overflow: hidden;
    background: var(--page-bg);
  }
  .card {
    position: absolute; left: 100px; top: 224px;
    width: 1000px; height: 605px;
    background: var(--card-bg);
    border-radius: 4px;
    box-shadow: 0 10px 30px rgba(0,0,0,0.12);
    overflow: hidden;
  }
  .brand {
    position: absolute; left: 51px; top: 52px; width: 652px;
    color: var(--brand-blue);
    font-family: "Montserrat", sans-serif; font-weight: 600;
  }
  .brand-name {
    font-size: 40px; letter-spacing: -0.5px; white-space: nowrap;
    line-height: 1;
  }
  .brand-sub {
    display: flex; align-items: center; gap: 20px; margin-top: 22px;
    font-size: 36px; letter-spacing: 10px; line-height: 1;
  }
  .brand-sub .rule {
    flex: 1; height: 4px; background: var(--brand-blue);
  }
  .info-band {
    position: absolute; left: 0; top: 240px;
    width: 100%; height: 267px;
    background: var(--band-blue);
  }
  .person-name {
    position: absolute; left: 51px; top: 32px;
    font-family: "Fira Sans Condensed", sans-serif; font-weight: 500;
    font-size: 41px; color: var(--band-text); line-height: 1;
  }
  .person-role {
    position: absolute; left: 51px; top: 83px;
    font-family: "Nunito Sans", sans-serif; font-size: 25px;
    color: var(--band-muted); line-height: 1;
  }
  .contact-list {
    position: absolute; left: 55px; top: 138px; list-style: none;
    font-family: "Montserrat", sans-serif; font-weight: 500;
    font-size: 23px; color: var(--band-text);
  }
  .contact-list li {
    display: flex; align-items: center; height: 35px;
  }
  .contact-list svg {
    width: 22px; height: 22px; margin-right: 26px; flex: none;
    fill: var(--band-muted);
  }
  .address {
    position: absolute; left: 51px; top: 539px;
    font-family: "Montserrat", sans-serif; font-weight: 500;
    font-size: 23px; color: var(--ink);
  }
</style>
</head>
<body>
  <div class="card">
    <header class="brand">
      <div class="brand-name">HARBORLIGHT AMUSEMENT</div>
      <div class="brand-sub"><span class="rule"></span><span>COLLECTIVE</span><span class="rule"></span></div>
    </header>

    <section class="info-band">
      <div class="person-name">Avery Lane Morgan</div>
      <div class="person-role">Managing Director</div>
      <ul class="contact-list">
        <li>
          <svg viewBox="0 0 24 24" aria-hidden="true"><path d="M3 8c0-2 4-4 9-4s9 2 9 4v2h-5V8H8v2H3z"/><path d="M5 12h14l1 8H4z"/></svg>
          555.014.2280
        </li>
        <li>
          <svg viewBox="0 0 24 24" aria-hidden="true"><path d="M2 5h20v14H2z M4 7v.5l8 6 8-6V7z"/></svg>
          avery@harborlightac.com
        </li>
        <li>
          <svg viewBox="0 0 24 24" aria-hidden="true"><circle cx="12" cy="12" r="10"/><path d="M2 12h20M12 2c-4 4-4 16 0 20M12 2c4 4 4 16 0 20" stroke="#2a5a98" stroke-width="1.5" fill="none"/></svg>
          www.harborlightac.com
        </li>
      </ul>
    </section>

    <footer class="address">418 Quayside Row, Port Merrow, US 204519</footer>
  </div>
</body>
</html>
```